Modern Business Card For A Digital Advertising Company

I'll be print on the Pell Prints Velour paper http://us.pellprints.com/products/velour/business-cards.html
Need's to be modern and use the color palette of the logo or gray scales. I think integrating the pixelation of the logo in to the card and having it wrap from one side to the other could be interesting. My company provides ad operations, web development, and number of other services to websites around the world. You can see my website at http://www.zantorhq.com
Contact info on the card needs to have
Owen Lasko
President
p.318.204.6637
owen@zantorhq.com
http://www.zantorhq.com
Doesn't necessarily need to be in that order
Website owners
Business

```html
<!DOCTYPE html>
<html lang="en">
<head>
<meta charset="utf-8">
<title>Zantor HQ – Business Card</title>
<link rel="stylesheet" href="https://fonts.googleapis.com/css2?family=Open+Sans:wght@400;600;700&display=swap">
<style>
  :root {
    --bg: #1e1e1e;
    --card-white: #ffffff;
    --green: #8cc63f;
    --green-deep: #5f8f34;
    --ink: #3a3a3a;
    --ink-soft: #555555;
    --swoosh: #333333;
    --divider: #c8c8c8;
  }
  * { margin: 0; padding: 0; box-sizing: border-box; }
  html, body {
    width: 1200px; height: 757px; overflow: hidden;
    background: var(--bg);
    font-family: "Open Sans", sans-serif;
  }
  .stage { position: relative; width: 1200px; height: 757px; }

  .card {
    position: absolute; top: 218px;
    width: 540px; height: 320px;
    border-radius: 26px; overflow: hidden;
    box-shadow: 0 14px 30px rgba(0,0,0,.55);
  }
  .card-front { left: 40px; background: var(--card-white); }
  .card-back {
    left: 620px;
    background: linear-gradient(160deg, var(--green-deep) 0%, var(--green) 100%);
  }

  .front-wave { position: absolute; inset: 0; width: 540px; height: 320px; }

  .brand {
    position: absolute; left: 46px; top: 70px; width: 200px;
    display: flex; align-items: center; gap: 12px;
  }
  .brand-square { width: 26px; height: 26px; background: var(--green); flex: none; }
  .brand-name {
    font-weight: 700; font-size: 30px; color: var(--green);
    letter-spacing: 1px; line-height: 1;
  }

  .divider {
    position: absolute; left: 262px; top: 34px;
    width: 2px; height: 110px; background: var(--divider);
  }

  .contacts {
    position: absolute; left: 282px; top: 40px;
    list-style: none; font-size: 14px; color: var(--ink-soft);
  }
  .contacts li { display: flex; align-items: center; gap: 9px; height: 27px; }
  .contacts svg { width: 13px; height: 13px; fill: var(--ink); flex: none; }

  .person {
    position: absolute; left: 46px; bottom: 26px;
    color: #fff; font-size: 19px; font-weight: 700; letter-spacing: .3px;
  }
  .person .role { font-size: 13px; font-weight: 400; letter-spacing: 0; }

  .back-brand {
    position: absolute; left: 0; right: 0; top: 104px;
    display: flex; justify-content: center; align-items: center; gap: 18px;
  }
  .back-brand .brand-square { width: 44px; height: 44px; background: #fff; }
  .back-brand .brand-name { color: #fff; font-size: 58px; letter-spacing: 2px; }

  .back-url {
    position: absolute; left: 0; right: 0; bottom: 56px;
    text-align: center; color: #fff;
    font-size: 21px; font-weight: 700; letter-spacing: 1.5px;
  }
</style>
</head>
<body>
<main class="stage">

  <section class="card card-front" aria-label="Card front">
    <svg class="front-wave" viewBox="0 0 540 320" aria-hidden="true">
      <defs>
        <linearGradient id="band" x1="0" y1="0" x2="1" y2="0">
          <stop offset="0" stop-color="#5f8f34"/>
          <stop offset="1" stop-color="#8cc63f"/>
        </linearGradient>
      </defs>
      <path d="M0 252 C160 196 360 246 540 168 L540 182 C360 256 160 212 0 266 Z" fill="#333333"/>
      <path d="M0 264 C160 212 360 258 540 184 L540 320 L0 320 Z" fill="url(#band)"/>
    </svg>

    <div class="brand">
      <span class="brand-square"></span>
      <span class="brand-name">ZANTOR HQ</span>
    </div>

    <div class="divider"></div>

    <ul class="contacts">
      <li>
        <svg viewBox="0 0 24 24"><path d="M6.6 10.8a15.5 15.5 0 0 0 6.6 6.6l2.2-2.2a1 1 0 0 1 1-.25 11.4 11.4 0 0 0 3.6.6 1 1 0 0 1 1 1V20a1 1 0 0 1-1 1A17 17 0 0 1 3 4a1 1 0 0 1 1-1h3.5a1 1 0 0 1 1 1c0 1.25.2 2.45.6 3.6a1 1 0 0 1-.25 1z"/></svg>
        318.204.6637
      </li>
      <li>
        <svg viewBox="0 0 24 24"><path d="M2 5h20v14H2z M4 7v.5l8 5 8-5V7l-8 5z" fill-rule="evenodd"/></svg>
        owen@zantorhq.com
      </li>
      <li>
        <svg viewBox="0 0 24 24"><circle cx="12" cy="12" r="10"/></svg>
        www.zantorhq.com
      </li>
    </ul>

    <p class="person">OWEN LASKO, <span class="role">President</span></p>
  </section>

  <section class="card card-back" aria-label="Card back">
    <div class="back-brand">
      <span class="brand-square"></span>
      <span class="brand-name">ZANTOR HQ</span>
    </div>
    <p class="back-url">www.zantorhq.com</p>
  </section>

</main>
</body>
</html>
```